We need a logo design for 2 new business card. One design for two brands "Op Koers" and TRV Kennisbron. We are looking for a creative and fun way to show our clients that we are one company. De color Red is te color of "Op Koers" The color orange (FF6600) is the color for TRV Kennisbron. in combination with the color white. Font is Sikina (google).
Both brands are working for entrepreneurs en small business owners in the Netherlands. Op Koers is a magazine and TRV Kennisbron is a online platform where business owners can download white papers, books, do scans and can read artikels about entrepreneurship.
our pay of is : Antwoord op ondernemers vragen

```html
<!DOCTYPE html>
<html lang="nl">
<head>
<meta charset="utf-8">
<title>Op Koers &amp; TRV Kennisbron – visitekaartjes</title>
<link rel="stylesheet" href="https://fonts.googleapis.com/css2?family=Ubuntu:wght@400;500;700&display=swap">
<style>
  :root {
    --orange: #ff6600;
    --red: #d7141a;
    --ink: #1e1c1c;
    --paper: #ffffff;
    --stage: #d9d9d9;
    --muted: #3a3a3a;
    --map-on-ink: #2e2c2c;
    --map-on-paper: #ececec;
  }
  * { margin: 0; padding: 0; box-sizing: border-box; }
  html, body { width: 1200px; height: 1000px; overflow: hidden; }
  body {
    background: var(--stage);
    font-family: "Ubuntu", sans-serif;
    position: relative;
  }
  .card {
    position: absolute;
    background: var(--paper);
    overflow: hidden;
    box-shadow: 0 6px 18px rgba(0,0,0,.18);
  }

  /* Contact card: Op Koers, red */
  .card-contact { left: 60px; top: 320px; width: 630px; height: 360px; }
  .contact-band {
    position: absolute; left: 0; top: 45px; width: 100%; height: 155px;
    background: var(--ink);
  }
  .contact-map {
    position: absolute; left: 410px; top: 120px; width: 200px; height: 180px;
    background: linear-gradient(180deg, var(--map-on-ink) 0%, var(--map-on-ink) 44%, var(--map-on-paper) 44%, #f5f5f5 100%);
  }
  .name-tag {
    position: absolute; left: 40px; top: 28px; width: 232px; height: 60px;
    background: var(--red); border-radius: 10px;
    padding: 10px 0 0 36px;
  }
  .name-tag .person { color: var(--paper); font-weight: 700; font-size: 20px; line-height: 1; }
  .name-tag .role { color: var(--ink); font-weight: 500; font-size: 14px; margin-top: 4px; }
  .direct-line {
    position: absolute; left: 76px; top: 106px; color: var(--paper);
    font-size: 16px; line-height: 24px; letter-spacing: .3px;
  }
  .direct-line .phone { font-weight: 500; }
  .office {
    position: absolute; left: 76px; top: 232px; color: var(--muted);
    font-size: 14px; line-height: 27px;
  }
  .office .row { display: flex; align-items: center; gap: 10px; }
  .office svg { width: 17px; height: 14px; flex: none; }

  /* Brand card: TRV Kennisbron, orange */
  .card-brand { left: 760px; top: 185px; width: 360px; height: 630px; }
  .brand-strip {
    position: absolute; left: 0; top: 0; width: 140px; height: 100%;
    background: var(--ink);
  }
  .brand-map {
    position: absolute; left: 235px; top: 30px; width: 110px; height: 500px;
    background: linear-gradient(180deg, #efefef 0%, #e4e4e4 50%, #f4f4f4 100%);
  }
  .brand-name {
    position: absolute; left: 160px; top: 70px;
    writing-mode: vertical-rl;
    color: var(--orange); font-weight: 700; font-size: 54px; letter-spacing: -1px;
    line-height: 1;
    display: flex; align-items: center; gap: 14px;
  }
  .brand-mark { width: 24px; height: 24px; background: var(--orange); }
  .brand-web {
    position: absolute; left: 92px; top: 150px;
    writing-mode: vertical-rl;
    color: var(--paper); font-size: 18px; letter-spacing: .5px;
  }
</style>
</head>
<body>

<section class="card card-contact">
  <div class="contact-band"></div>
  <div class="contact-map" role="img" aria-label="Dotted world map decoration"></div>
  <div class="name-tag">
    <div class="person">Sanne Verhoef</div>
    <div class="role">accountant</div>
  </div>
  <div class="direct-line">
    <div class="phone">+31 20 555 0142</div>
    <div class="email">sanne@opkoers.nl</div>
  </div>
  <div class="office">
    <div class="row">12 Keizersgracht, 1015 Amsterdam, Nederland</div>
    <div class="row">
      <svg viewBox="0 0 17 14" aria-hidden="true"><rect width="17" height="14" fill="#1e1c1c"/><path d="M4 3c0 4 4 8 8 8l1-2-2-1-1 1c-1-.5-2.5-2-3-3l1-1-1-2z" fill="#fff"/></svg>
      +31 (0) 20 555 0100
    </div>
    <div class="row">
      <svg viewBox="0 0 17 14" aria-hidden="true"><rect width="17" height="14" fill="#1e1c1c"/><rect x="3" y="3.5" width="11" height="7" fill="none" stroke="#fff" stroke-width="1.2"/><path d="M3 3.5l5.5 4 5.5-4" fill="none" stroke="#fff" stroke-width="1.2"/></svg>
      info@opkoers.nl
    </div>
  </div>
</section>

<section class="card card-brand">
  <div class="brand-strip"></div>
  <div class="brand-map" role="img" aria-label="Dotted world map decoration"></div>
  <div class="brand-name"><span class="brand-mark"></span>trvkennisbron</div>
  <div class="brand-web">www.trvkennisbron.nl</div>
</section>

</body>
</html>
```